PWRPT design for Company

Project: Develop a pwrpt for QT7lx. This can be just a blank pwrpt with standard templates that we can use to build our content and solutions around.
Website: www.qt7lx.example
Color Pallet: Try to use the color schema from our website.
PWRPT Design Tips: While we are a research-based company, our primary target is schools and school districts. We say our work is RESEARCH, POLICY, AND PRACTICE. I would like images that represent “WHY” our research matters, i.e. students, teachers, and administrators. If you can use images and stock photos that represent students with diverse backgrounds, teachers that are diverse and clearly teaching, and administrators that run a school, university, etc. We are in the process of updating our website, but the color scheme will remain the same.
Additional Information:
We built, researched, and designed, www.brvo-kt.example .
We built, researched, and designed, http://67pwgamma.example/olar/index.html
Target Market(s)
EDUCATION
Industry/Entity Type
It Company
Look and feel

```html
<!DOCTYPE html>
<html lang="en">
<head>
<meta charset="utf-8">
<title>QT7lx — Welcome</title>
<link rel="stylesheet" href="https://fonts.googleapis.com/css2?family=Lato:wght@300;400;700;900&display=swap">
<style>
  :root {
    --orange: #f7941d;
    --white: #ffffff;
    --ink: #3a3a3a;
    --base-strip: #565c5d;
    --photo-light: #d9d2c8;
    --photo-mid: #a89d90;
    --photo-dark: #6f655c;
  }
  html, body {
    margin: 0;
    padding: 0;
    width: 1200px;
    height: 900px;
    overflow: hidden;
    background: var(--white);
    font-family: "Lato", Arial, sans-serif;
  }
  .slide {
    position: relative;
    width: 1200px;
    height: 900px;
    overflow: hidden;
  }
  .hero {
    position: absolute;
    top: 0;
    left: 0;
    width: 1200px;
    height: 735px;
  }
  .hero svg { display: block; }
  .title-block {
    position: absolute;
    left: 600px;
    top: 392px;
    color: var(--white);
  }
  .title-block .welcome {
    margin: 0;
    font-weight: 900;
    font-size: 62px;
    line-height: 1;
    letter-spacing: 0.5px;
  }
  .title-block .program {
    margin: 12px 0 0;
    font-weight: 400;
    font-size: 40px;
    line-height: 1.1;
  }
  .title-block .date {
    margin: 20px 0 0;
    font-weight: 400;
    font-size: 26px;
  }
  .footer {
    position: absolute;
    top: 735px;
    left: 0;
    width: 1200px;
    height: 143px;
    background: var(--white);
  }
  .footer .legal {
    position: absolute;
    left: 40px;
    top: 52px;
    width: 690px;
    margin: 0;
    font-size: 16px;
    line-height: 1.6;
    color: var(--ink);
  }
  .brand {
    position: absolute;
    right: 45px;
    top: 30px;
  }
  .brand .name-row {
    display: flex;
    align-items: center;
    gap: 14px;
  }
  .brand .mark {
    width: 44px;
    height: 44px;
    background: var(--orange);
  }
  .brand .name {
    font-size: 54px;
    font-weight: 400;
    line-height: 1;
    color: var(--ink);
  }
  .slogan {
    margin: 16px 0 0;
    font-size: 15px;
    font-weight: 400;
    letter-spacing: 1.2px;
    color: var(--ink);
    text-align: right;
  }
  .base-strip {
    position: absolute;
    left: 0;
    bottom: 0;
    width: 1200px;
    height: 22px;
    background: var(--base-strip);
  }
</style>
</head>
<body>
  <main class="slide">
    <section class="hero">
      <svg width="1200" height="735" viewBox="0 0 1200 735">
        <defs>
          <linearGradient id="photoTone" x1="0" y1="0" x2="1" y2="1">
            <stop offset="0" stop-color="#d9d2c8"/>
            <stop offset="0.5" stop-color="#a89d90"/>
            <stop offset="1" stop-color="#6f655c"/>
          </linearGradient>
          <linearGradient id="orangeVeil" x1="0" y1="0" x2="1" y2="0">
            <stop offset="0" stop-color="#f7941d" stop-opacity="0.97"/>
            <stop offset="1" stop-color="#f7941d" stop-opacity="0.82"/>
          </linearGradient>
        </defs>
        <rect class="hero-photo" width="1200" height="735" fill="url(#photoTone)"
              role="img" aria-label="Photo of diverse students studying together around a table with notebooks and laptops"/>
        <polygon class="hero-panel" points="705,0 1200,0 1200,735 382,735" fill="url(#orangeVeil)"/>
      </svg>
      <div class="title-block">
        <h1 class="welcome">WELCOME</h1>
        <p class="program">Bridge2Futures (B2F)</p>
        <p class="date">August 21st, 2017</p>
      </div>
    </section>

    <footer class="footer">
      <p class="legal">© 2017 All rights reserved. Contains confidential and proprietary information and may not be disclosed or reproduced without &nbsp;the prior written consent of QT7lx</p>
      <div class="brand">
        <div class="name-row">
          <span class="mark" aria-hidden="true"></span>
          <span class="name">QT7lx</span>
        </div>
        <p class="slogan">STUDY + PLAN + TEACH</p>
      </div>
    </footer>
    <div class="base-strip"></div>
  </main>
</body>
</html>
```